real estate managers brochure A5

Real estate services brochure (owners corporation management)

Content has been uploaded in MS word documents and we reserve the right to refine the text in one revision.

Visit out site http://www.marrowfen.com.au/body-corporate-managers/ and review the pages in the 'owners corporation' menu in our website - the brochure is for these services we provide.

We want to showcase a variety of 'trophy' buildings/unit/apartment/factory developments that we manage - I've uploaded these 'case studies' and high res images for each.

Some General services photos to be provided by you.

The brochure is given out to potential owners who we wish to be clients.

We are going to print a few dozen of these in hard copy so will need artwork in nigh resolution pdf format and a web resolution version for emailing potential clients.

Target Market(s)

Unit owners, apartment owners and commercial factory owners

Industry/Entity Type

Property Management

Font styles to use
Serif
Sans Serif

Requirements
Must have
• A modern design that looks like it could be just as home on a website or facebook post
• Have a flair of retro design and/or vintage graphics
• 3 full pages of example properties we manage property. see example properties in the case studies. I have uploaded high res images for the full page images and some brief text for these pages
Should not have
• Must not look like a typical real estate agents brochure (smiling agents, happy home owners)
• Images of people who do not look australian (ie afro american, asian) as this is not our target market. We typically have anglo australian or eruopean looking clients
• We are a young company who pride ourselves on. Efficient services and high tech management systems for the properties we manage

```html
<!DOCTYPE html>
<html lang="en">
<head>
<meta charset="utf-8">
<title>Management services – Marrowfen</title>
<link rel="stylesheet" href="https://fonts.googleapis.com/css2?family=Raleway:wght@300;400&family=Source+Serif+4:wght@600&display=swap">
<style>
  :root {
    --brand-blue: #3b4c9b;
    --text-grey: #4a4a4a;
    --heading-grey: #3d3d3d;
    --page-bg: #ffffff;
  }
  * { margin: 0; padding: 0; box-sizing: border-box; }
  html, body {
    width: 928px;
    height: 1200px;
    overflow: hidden;
    background: var(--page-bg);
  }
  .page {
    position: relative;
    width: 928px;
    height: 1200px;
    font-family: "Raleway", Arial, sans-serif;
    font-weight: 400;
    color: var(--text-grey);
    font-size: 19.5px;
    line-height: 26px;
  }
  .page-title {
    position: absolute;
    left: 84px;
    top: 26px;
    font-family: "Raleway", Arial, sans-serif;
    font-weight: 300;
    font-size: 56px;
    line-height: 64px;
    color: var(--brand-blue);
    letter-spacing: 0.3px;
  }
  .title-rule {
    position: absolute;
    left: 0;
    top: 86px;
  }
  .column {
    position: absolute;
    top: 136px;
  }
  .column--left { left: 86px; width: 400px; }
  .column--right { left: 540px; width: 350px; top: 128px; }
  .intro { margin-bottom: 24px; }
  .section-heading {
    font-family: "Source Serif 4", Georgia, serif;
    font-weight: 600;
    font-size: 23px;
    line-height: 30px;
    color: var(--heading-grey);
    margin-bottom: 12px;
  }
  .service-list {
    list-style: none;
    margin-bottom: 28px;
  }
  .service-list li {
    position: relative;
    padding-left: 44px;
    margin-bottom: 12px;
  }
  .service-list li::before {
    content: "";
    position: absolute;
    left: 16px;
    top: 10px;
    width: 6px;
    height: 6px;
    border-radius: 50%;
    background: var(--text-grey);
  }
</style>
</head>
<body>
<main class="page">
  <h1 class="page-title">Management services</h1>
  <svg class="title-rule" width="640" height="20" viewBox="0 0 640 20" aria-hidden="true">
    <line x1="0" y1="10" x2="622" y2="10" stroke="var(--brand-blue)" stroke-width="2.5"/>
    <circle cx="623" cy="10" r="9" fill="var(--brand-blue)"/>
  </svg>

  <section class="column column--left">
    <p class="intro">MARROWFEN have developed a highly efficient management service with documented procedures and quality control.</p>

    <h2 class="section-heading">Communication &amp; Customer Service</h2>
    <ul class="service-list">
      <li>Facilitate communication between owners, the Committee and residents</li>
      <li>Acknowledge the receipt of and respond to all correspondence promptly</li>
      <li>Maintain accurate records of all business conducted on your behalf</li>
      <li>Prepare and distribute all meeting notices, agendas and supporting documents</li>
      <li>Distribute minutes of Owners Corporation meetings</li>
    </ul>

    <h2 class="section-heading">Management</h2>
    <ul class="service-list">
      <li>Invoice statutory fee notices to Lot owners</li>
      <li>Ensure arrears and debts are efficiently managed</li>
      <li>Pay invoices and accounts as authorised</li>
      <li>Arrange and maintain insurance policies and valuations</li>
      <li>Arrange safety audits and building reports &nbsp;as required</li>
      <li>General asset management, arrange and coordinate contractors</li>
    </ul>
  </section>

  <section class="column column--right">
    <ul class="service-list">
      <li>Report to the committee and members at your Annual General Meeting</li>
    </ul>

    <h2 class="section-heading">Financial</h2>
    <ul class="service-list">
      <li>Maintain the Owners Corporation bank accounts, (daily reconciliation)</li>
      <li>Receipt and bank all levies</li>
      <li>Manage and remit tax and other duties</li>
      <li>Provide financial statements and reports to your Committee as required</li>
      <li>Prepare an annual budget for admin. and maintenance funds</li>
    </ul>

    <h2 class="section-heading">Services</h2>
    <ul class="service-list">
      <li>Conduct the annual general meeting</li>
      <li>Support the operation of the Owners Corporation Committee</li>
      <li>Guide you to comply with the Owners Corporations Act, Regulations and your Rules</li>
      <li>Maintain the owners corporation register</li>
      <li>Implement and operate a grievance procedure</li>
      <li>Provide prompt attention to authorised requests</li>
      <li>Custody and use of/affixing common seal</li>
    </ul>
  </section>
</main>
</body>
</html>
```